Bramwell Specialty Coffee needs a Packaging design

We need packaging design for coffee that suits our brand identity, that is the best quality in Mexico.
We only sell mexican coffee with Q scores above 80
We are evaluating 3 types of packaging: Bag, Box and Cillinder can
The specific package format will be decided based on the designs that we get.

Target Market(s)

Coffee experts and enthusiast.
People that relate the Coffee consumption and experience with wine tasting and Bon Vivant way

Requirements
Should not have
• Photos any mexican cliché

```html
<!DOCTYPE html>
<html lang="en">
<head>
<meta charset="utf-8">
<title>Bramwell Specialty Coffee — Packaging Label</title>
<link rel="stylesheet" href="https://fonts.googleapis.com/css2?family=Cormorant+Garamond:wght@600&family=Tinos&display=swap">
<style>
  :root {
    --page: #ffffff;
    --gold-light: #f3ebdd;
    --gold-mid: #d9c2a0;
    --gold-deep: #a87b45;
    --bronze: #7a4a2e;
    --roast: #3a2418;
    --ink: #1f140d;
    --band-light: #c9a26e;
    --band: #b08650;
    --band-dark: #5e4020;
  }
  * { box-sizing: border-box; margin: 0; padding: 0; }
  html, body {
    width: 1200px;
    height: 1000px;
    overflow: hidden;
    background: var(--page);
  }
  .canvas {
    position: relative;
    width: 1200px;
    height: 1000px;
    overflow: hidden;
    background: var(--page);
  }
  .label {
    position: absolute;
    left: 0;
    top: 20px;
    width: 1200px;
    height: 782px;
    background:
      radial-gradient(ellipse 60% 65% at 45% 55%, var(--gold-light) 0%, var(--gold-mid) 55%, var(--gold-deep) 100%);
  }
  .key-band {
    position: absolute;
    left: 0;
    width: 1200px;
    height: 86px;
    background: linear-gradient(180deg, var(--band) 0%, var(--band-light) 50%, var(--band) 100%);
    border-top: 3px solid var(--band-dark);
    border-bottom: 3px solid var(--band-dark);
  }
  .key-band::before,
  .key-band::after {
    content: "";
    position: absolute;
    left: 0;
    right: 0;
    height: 0;
    border-top: 1px solid var(--band-dark);
    opacity: 0.7;
  }
  .key-band::before { top: 6px; }
  .key-band::after { bottom: 6px; }
  .key-band__field {
    position: absolute;
    left: 0;
    right: 0;
    top: 14px;
    bottom: 14px;
    background: linear-gradient(180deg, #a67a44 0%, #c39a63 50%, #a67a44 100%);
    box-shadow: inset 0 2px 3px rgba(60, 35, 15, 0.45), inset 0 -2px 3px rgba(255, 240, 210, 0.35);
  }
  .key-band--top { top: 0; }
  .key-band--bottom { top: 694px; }

  .brand-dot {
    position: absolute;
    left: 300px;
    top: 150px;
    width: 200px;
    height: 200px;
    border-radius: 50%;
    background: var(--bronze);
    opacity: 0.85;
  }
  .wordmark {
    position: absolute;
    left: 590px;
    top: 168px;
    width: 550px;
    text-align: center;
    font-family: "Cormorant Garamond", Georgia, serif;
    font-weight: 600;
    color: var(--bronze);
    line-height: 1;
  }
  .wordmark__name {
    display: block;
    font-size: 130px;
  }
  .wordmark__tagline {
    display: block;
    margin-top: 20px;
    margin-left: 50px;
    font-size: 54px;
  }
  .bean-art {
    position: absolute;
    left: 830px;
    top: 360px;
    width: 330px;
    height: 290px;
  }
  .roast-note {
    position: absolute;
    left: 872px;
    top: 566px;
    font-family: "Tinos", "Times New Roman", serif;
    font-size: 13px;
    color: var(--gold-light);
    transform: rotate(14deg);
    transform-origin: left center;
  }
  .net-weight {
    position: absolute;
    left: 465px;
    top: 650px;
    width: 440px;
    text-align: center;
    font-family: "Tinos", "Times New Roman", serif;
    font-size: 30px;
    color: var(--ink);
  }
</style>
</head>
<body>
  <main class="canvas">
    <section class="label" aria-label="Bramwell Specialty Coffee label">
      <div class="key-band key-band--top" role="img" aria-label="Embossed meander border band">
        <div class="key-band__field"></div>
      </div>

      <div class="brand-dot" aria-hidden="true"></div>
      <h1 class="wordmark">
        <span class="wordmark__name">Bramwell</span>
        <span class="wordmark__tagline">Specialty Coffee</span>
      </h1>

      <svg class="bean-art" viewBox="0 0 330 290" role="img" aria-label="Stylised coffee bean illustration">
        <defs>
          <radialGradient id="bean-tone" cx="45%" cy="40%" r="65%">
            <stop offset="0%" stop-color="#8a6a55"/>
            <stop offset="100%" stop-color="#3a2418"/>
          </radialGradient>
        </defs>
        <ellipse cx="165" cy="160" rx="160" ry="105" transform="rotate(-20 165 160)" fill="url(#bean-tone)" opacity="0.85"/>
      </svg>
      <p class="roast-note">Special Bold Dark Roast</p>

      <p class="net-weight">NET WT 33.9 OZ(0.95kg)</p>

      <div class="key-band key-band--bottom" role="img" aria-label="Embossed meander border band">
        <div class="key-band__field"></div>
      </div>
    </section>
  </main>
</body>
</html>
```